Business Card Design Project

Looking to update our business cards. We have a logo with our slogan. We are an IT firm so we wouldlike a modern look.

Industry/Entity Type

Business

```html
<!DOCTYPE html>
<html lang="en">
<head>
<meta charset="utf-8">
<title>Nordvale Business Card Set</title>
<link rel="stylesheet" href="https://fonts.googleapis.com/css2?family=Jost:wght@500;600&family=Montserrat:wght@700&family=Open+Sans:wght@400;600&display=swap">
<style>
  :root {
    --stage: #8a5b36;
    --label: #1c130c;
    --card-white: #ffffff;
    --olive: #687f3f;
    --olive-text: #6b8a3a;
    --lime: #a9c33b;
    --lime-card: #b0c445;
    --ink: #333333;
    --divider: #8c8c8c;
    --glow-core: #eef3ff;
    --glow-mid: #6f95e0;
    --glow-edge: #16357e;
  }
  * { margin: 0; padding: 0; box-sizing: border-box; }
  html, body { width: 1200px; height: 788px; overflow: hidden; }
  body { background: var(--stage); position: relative; font-family: "Open Sans", sans-serif; }

  .view-label {
    position: absolute; width: 300px; text-align: center;
    font-family: "Open Sans", sans-serif; font-size: 21px; color: var(--label);
  }

  .card {
    position: absolute; width: 526px; height: 298px;
    border-radius: 22px; overflow: hidden;
    box-shadow: 0 3px 8px rgba(0,0,0,0.35);
  }
  .card--front { left: 52px; top: 82px; background: var(--card-white); }
  .card--back-white { left: 620px; top: 80px; background: var(--card-white); }
  .card--back-lime { left: 50px; top: 455px; background: var(--lime-card); }
  .card--back-tech { left: 620px; top: 455px; }

  .brand { position: absolute; text-align: center; color: var(--olive); }
  .brand__name {
    font-family: "Jost", sans-serif; font-weight: 600;
    letter-spacing: 6px; line-height: 1;
  }
  .brand__tagline {
    font-family: "Montserrat", sans-serif; font-weight: 700;
    color: var(--ink); line-height: 1;
  }
  .brand--small { left: 30px; top: 98px; width: 230px; }
  .brand--small .brand__name { font-size: 34px; }
  .brand--small .brand__tagline { font-size: 10px; letter-spacing: 1.6px; margin-top: 4px; }
  .brand--large { left: 0; width: 100%; top: 118px; }
  .brand--large .brand__name { font-size: 50px; letter-spacing: 9px; }
  .brand--large .brand__tagline { font-size: 13.5px; letter-spacing: 3px; margin-top: 6px; }

  .divider { position: absolute; left: 274px; top: 50px; width: 1px; height: 133px; background: var(--divider); }

  .contact { position: absolute; left: 298px; top: 50px; color: var(--ink); }
  .contact__name { font-family: "Jost", sans-serif; font-weight: 600; font-size: 19px; color: var(--olive-text); line-height: 22px; }
  .contact__role { font-size: 13.5px; color: var(--olive-text); line-height: 18px; }
  .contact__list { list-style: none; margin-top: 17px; font-size: 13.5px; line-height: 18.5px; }
  .contact__key { font-weight: 600; font-style: italic; }

  .footer-bands { position: absolute; left: 0; bottom: 0; width: 526px; height: 60px; }
  .address { position: absolute; left: 298px; top: 251px; color: #fff; font-size: 13.5px; line-height: 18px; }

  .tech-backdrop {
    position: absolute; inset: 0;
    background:
      radial-gradient(ellipse 45% 55% at 52% 55%, var(--glow-core) 0%, rgba(180,205,250,0.9) 30%, rgba(111,149,224,0.4) 60%, transparent 80%),
      linear-gradient(90deg, var(--glow-edge) 0%, #2f5cc4 30%, #5a7fd8 55%, #2b56b8 80%, var(--glow-edge) 100%);
  }
</style>
</head>
<body>

  <div class="view-label" style="left:170px; top:32px;">Front</div>
  <div class="view-label" style="left:746px; top:32px;">Back - 1</div>
  <div class="view-label" style="left:174px; top:402px;">Back - 2</div>
  <div class="view-label" style="left:746px; top:402px;">Back - 3</div>

  <section class="card card--front">
    <div class="brand brand--small">
      <div class="brand__name">NORDVALE</div>
      <div class="brand__tagline">MAKING TECH WORK FOR YOU</div>
    </div>
    <div class="divider"></div>
    <div class="contact">
      <div class="contact__name">Your Name</div>
      <div class="contact__role">Designation</div>
      <ul class="contact__list">
        <li><span class="contact__key">p</span> : +12 345 67890</li>
        <li><span class="contact__key">f</span> : +12 345 67890</li>
        <li><span class="contact__key">e</span> : info@website.com</li>
        <li><span class="contact__key">w</span> : www.website.com</li>
      </ul>
    </div>
    <svg class="footer-bands" viewBox="0 0 526 60" aria-hidden="true">
      <polygon points="0,26 258,26 246,36 0,36" fill="var(--lime)"/>
      <polygon points="290,0 526,0 526,60 240,60" fill="var(--olive)"/>
    </svg>
    <div class="address">#0000, Street Name<br>Area Name, Country</div>
  </section>

  <section class="card card--back-white">
    <div class="brand brand--large">
      <div class="brand__name">NORDVALE</div>
      <div class="brand__tagline">MAKING TECH WORK FOR YOU</div>
    </div>
  </section>

  <section class="card card--back-lime">
    <div class="brand brand--large">
      <div class="brand__name">NORDVALE</div>
      <div class="brand__tagline">MAKING TECH WORK FOR YOU</div>
    </div>
  </section>

  <section class="card card--back-tech">
    <div class="tech-backdrop" role="img" aria-label="Abstract blue technology backdrop with glowing light rings, binary digits and a wireframe globe"></div>
    <div class="brand brand--large">
      <div class="brand__name">NORDVALE</div>
      <div class="brand__tagline">MAKING TECH WORK FOR YOU</div>
    </div>
  </section>

</body>
</html>
```